Keystonery Billboard - Financial Services Company (Investments, Tax Planning and Insurance)

Our new office has a billboard directly above the office building. We'd like something eye-catching with a strong Call to Action, with the main part of the billboard being under 7 words if possible. We'd like you to include a way to get ahold of us (either our website keystoneryllc.example or our phone number 302-418-2907. You may also include in small font something to indicate that we've been serving the area since 1980 (the DE area, the tri-state area, the Marlowe Hollow, etc.)

We offer financial planning, tax planning, and insurance, and we help our clients to focus on their goals and happiness by providing everything they need for lifelong wealth under one roof.

Our logos are attached, we use a triangle logo with green and gray. We use the tagline "discover lasting prosperity" but this does not need to be included.

Potential ideas we have seen from other financial companies-
- the concept that the driver spends more time looking at billboards than planning for their retirement
-something along the lines of "everything you need for your finances is in this building right here" planning, investments, taxes, insurance"
-don't spend your time worrying about retirement, let us help you plan for it
-are you working for your money, or is it working for you?
- retirement takes planning, we're here to help
- ready to retire? talk to us
- need investment advice?
- need help investing?
- crossing your fingers isn't a retirement plan. we can help.
- retiring soon? you need help.

Those are just general ideas, please feel free to be creative.

brand colors:
#00b585
#00b185
#000000
#ffffff
#6d6f75
#6d6f75
#6f7074
#021712
#052e24

```html
<!DOCTYPE html>
<html lang="en">
<head>
<meta charset="UTF-8">
<title>Keystonery Billboard</title>
<link rel="stylesheet" href="https://fonts.googleapis.com/css2?family=Anton&family=Oswald:wght@500;600&display=swap">
<style>
  :root {
    --backdrop: #1c1f22;
    --paper: #ffffff;
    --brand-green: #009962;
    --brand-gray: #5f6067;
    --deep-green: #03291f;
    --band-gray: #76777b;
    --photo-light: #eeebe7;
    --photo-mid: #cfc9c2;
    --photo-cool: #9fa6b0;
    --photo-dark: #3b4047;
  }
  html, body {
    margin: 0;
    padding: 0;
    width: 1200px;
    height: 800px;
    overflow: hidden;
    background: var(--backdrop);
  }
  .canvas {
    position: relative;
    width: 1200px;
    height: 800px;
    background: var(--backdrop);
  }
  .billboard {
    position: absolute;
    left: 0;
    top: 200px;
    display: block;
  }
  .brand-name { font-family: "Oswald", sans-serif; font-weight: 600; fill: var(--brand-green); }
  .brand-tagline { font-family: "Oswald", sans-serif; font-weight: 500; fill: var(--brand-gray); letter-spacing: 3.4px; }
  .headline { font-family: "Anton", sans-serif; }
  .headline--green { fill: var(--brand-green); }
  .headline--gray { fill: var(--brand-gray); }
  .call-to-action { font-family: "Anton", sans-serif; fill: var(--deep-green); }
  .bullet { fill: var(--brand-green); }
  .since-note, .contact-text { font-family: "Oswald", sans-serif; font-weight: 600; fill: var(--paper); }
  .contact-band, .photo-frame { fill: var(--band-gray); }
  .icon-fill { fill: var(--paper); }
  .icon-line { fill: none; stroke: var(--band-gray); stroke-width: 1.4; }
  .icon-globe { fill: none; stroke: var(--paper); stroke-width: 1.3; }
</style>
</head>
<body>
<div class="canvas">
  <svg class="billboard" width="1200" height="400" viewBox="0 0 1200 400" xmlns="http://www.w3.org/2000/svg">
    <defs>
      <linearGradient id="photoTone" x1="0" y1="0" x2="1" y2="1">
        <stop offset="0" stop-color="var(--photo-light)"/>
        <stop offset="0.45" stop-color="var(--photo-mid)"/>
        <stop offset="0.8" stop-color="var(--photo-cool)"/>
        <stop offset="1" stop-color="var(--photo-dark)"/>
      </linearGradient>
    </defs>

    <rect class="panel" x="0" y="0" width="1200" height="400" fill="var(--paper)"/>

    <!-- photo side -->
    <path class="photo-frame" d="M689,0 Q561,200 668,400 L1200,400 L1200,0 Z"/>
    <path class="photo-area" role="img" aria-label="Softly blurred photo of financial advisers reviewing bar charts and tables on a clipboard at an office desk"
          d="M695,0 Q587,190 672,366 L1200,366 L1200,0 Z" fill="url(#photoTone)"/>

    <text class="since-note" x="1172" y="37" text-anchor="end" font-size="22">SINCE 1980</text>

    <!-- contact band -->
    <rect class="contact-band" x="660" y="366" width="540" height="34"/>
    <g class="icon-phone" transform="translate(722,384)">
      <circle class="icon-fill" r="9"/>
      <path d="M-4,-4 q0,9 8,8 l1,-2 -3,-2 -1,1 q-3,-1 -4,-4 l1,-1 -2,-3 z" fill="var(--band-gray)"/>
    </g>
    <text class="contact-text" x="740" y="393" font-size="24" textLength="130" lengthAdjust="spacingAndGlyphs">302-418-2907</text>
    <g class="icon-globe" transform="translate(931,384)">
      <circle r="8.5"/>
      <ellipse rx="3.8" ry="8.5"/>
      <line x1="-8.5" y1="0" x2="8.5" y2="0"/>
      <path d="M-7,-4.5 H7 M-7,4.5 H7"/>
    </g>
    <text class="contact-text" x="949" y="393" font-size="24" textLength="223" lengthAdjust="spacingAndGlyphs">WWW.KEYSTONERYLLC.EXAMPLE</text>

    <!-- brand -->
    <g class="brand">
      <circle class="bullet" cx="196" cy="57" r="17"/>
      <text class="brand-name" x="224" y="71" font-size="42" textLength="206" lengthAdjust="spacingAndGlyphs">Keystonery</text>
      <text class="brand-tagline" x="226" y="84" font-size="8" textLength="202" lengthAdjust="spacing">DISCOVER LASTING PROSPERITY</text>
    </g>

    <!-- headline -->
    <text class="headline headline--green" x="57" y="183" font-size="84" textLength="513" lengthAdjust="spacingAndGlyphs">MINIMIZE STRESS</text>
    <text class="headline headline--gray" x="57" y="268" font-size="80" textLength="513" lengthAdjust="spacingAndGlyphs">MAXIMIZE WEALTH</text>

    <circle class="bullet" cx="121" cy="336" r="13"/>
    <text class="call-to-action" x="147" y="369" font-size="85" textLength="333" lengthAdjust="spacingAndGlyphs">CHOOSE US</text>
    <circle class="bullet" cx="508" cy="336" r="13"/>
  </svg>
</div>
</body>
</html>
```